Pemberlux: Smart Quotes for Wine Lovers

Hello. I am completing book of quotes for wine lovers. Need the text formatted so that it is easy to read and aesthetically pleasing...modern, clean, smart. Number the pages. The cover is complete. Book is small square. 7.5 by 7.5 inches. If you want to show me first few pages that would be awesome. Thank you!
Updates

I edited the quotes so if you downloaded first ones, please grab these ones instead, thank you! 

Target Market(s)

wine lovers. Urban. Modern.

Industry/Entity Type

Quotes

Requirements
Should not have
• No color. black and white only.

```html
<!DOCTYPE html>
<html lang="en">
<head>
<meta charset="utf-8">
<title>Pemberlux: Smart Quotes for Wine Lovers</title>
<link rel="stylesheet" href="https://fonts.googleapis.com/css2?family=Sorts+Mill+Goudy&family=Cabin:wght@400&family=Archivo+Narrow:wght@700&display=swap">
<style>
  :root {
    --ink: #000000;
    --paper: #ffffff;
  }
  html, body {
    margin: 0;
    padding: 0;
    width: 1200px;
    height: 600px;
    overflow: hidden;
    background: var(--paper);
  }
  .spread {
    position: relative;
    width: 1200px;
    height: 600px;
    display: flex;
  }
  .page {
    position: relative;
    height: 600px;
  }
  .page--verso {
    width: 601px;
    background: var(--ink);
    color: var(--paper);
  }
  .page--recto {
    width: 599px;
    background: var(--paper);
    color: var(--ink);
  }
  .quote {
    position: absolute;
    margin: 0;
    font-family: "Sorts Mill Goudy", "Goudy Old Style", serif;
    font-size: 35px;
    line-height: 45.5px;
    font-weight: 400;
    white-space: nowrap;
  }
  .page--verso .quote { left: 95px; top: 216px; }
  .page--recto .quote { right: 94px; top: 216px; text-align: right; }
  .attribution {
    position: absolute;
    margin: 0;
    font-family: "Cabin", "Gill Sans", sans-serif;
    font-size: 13px;
    line-height: 16px;
    letter-spacing: 0.08em;
    text-transform: uppercase;
  }
  .page--verso .attribution { left: 95px; top: 412px; }
  .page--recto .attribution { right: 93px; top: 405px; }
  .bio {
    position: absolute;
    top: 518px;
    margin: 0;
    font-family: "Archivo Narrow", "Helvetica Neue", sans-serif;
    font-weight: 700;
    font-size: 7.6px;
    line-height: 9.5px;
    white-space: nowrap;
  }
  .page--verso .bio { right: 49px; text-align: right; }
  .page--recto .bio { left: 62px; }
  .folio {
    position: absolute;
    right: 78px;
    top: 523px;
    margin: 0;
    font-family: "Cabin", "Gill Sans", sans-serif;
    font-size: 13px;
  }
</style>
</head>
<body>
  <main class="spread">
    <section class="page page--verso">
      <blockquote class="quote">The connoisseur<br>does not drink<br>wine but tastes its<br>secrets</blockquote>
      <p class="attribution">&mdash;Tomas Verrandell</p>
      <p class="bio">Tomas Esteban Verrandell i Soler, Catalan collector of old Priorat<br>vintages (1921-1994) Poet, Essayist and Gardener.</p>
    </section>
    <section class="page page--recto">
      <blockquote class="quote">Wine is the<br>divine juice of<br>September.</blockquote>
      <p class="attribution">&mdash;Castel</p>
      <p class="bio">Jean-Luc Armand Castel &nbsp;known to his friends simply as Castel.<br>(1802 -1871). Lyonnais Wine Merchant, Diarist and Keen Traveller.</p>
      <p class="folio">33</p>
    </section>
  </main>
</body>
</html>
```